business card - Helicopter Flight Services, Flight School, etc.

We need a business card design for a new helicopter service.

We offer Helicopter Flight Services, Aerial Filming & Photography, Flight School, and Helicopter Tours. In that order.

Summit BladeAir, Inc.
Dennis Tollerby
SummitBladeair@Kestmail.com
626-418-7352

Based at the Brenwick Airport in Van Nuys, CA. The final design should communicate integrity and safety. Pictures or logos at your discretion.

Card back side - surprise me.

```html
<!DOCTYPE html>
<html lang="en">
<head>
<meta charset="utf-8">
<title>Summit BladeAir, Inc. – Business Card</title>
<link rel="stylesheet" href="https://fonts.googleapis.com/css2?family=Open+Sans:wght@400;600;700&display=swap">
<style>
  :root {
    --page-bg: #e9e6e1;
    --card-black: #0b0b0c;
    --sky-blue: #2aa6e2;
    --sky-blue-light: #5cc6f0;
    --sky-blue-deep: #1a78c9;
    --leaf-green: #8fcb4a;
    --ink-dark: #1b1d1f;
    --white: #ffffff;
  }
  * { box-sizing: border-box; margin: 0; padding: 0; }
  html, body { width: 1200px; height: 913px; overflow: hidden; }
  body {
    background: var(--page-bg);
    font-family: "Open Sans", Arial, sans-serif;
    position: relative;
  }
  .card {
    position: absolute;
    width: 520px;
    height: 297px;
    border-radius: 3px;
    overflow: hidden;
    box-shadow: 0 6px 18px rgba(0,0,0,0.18);
  }
  .card-front { left: 50px; top: 308px; background: var(--card-black); }
  .card-back {
    left: 630px; top: 308px;
    background: linear-gradient(160deg, var(--sky-blue-light) 0%, var(--sky-blue) 55%, var(--sky-blue-deep) 100%);
  }
  .front-bands { position: absolute; inset: 0; }
  .brand {
    position: absolute;
    display: flex;
    align-items: center;
    gap: 10px;
    font-weight: 700;
    letter-spacing: 0.5px;
  }
  .brand-dot { width: 14px; height: 14px; border-radius: 50%; }
  .card-front .brand { left: 60px; top: 84px; font-size: 30px; color: var(--sky-blue); }
  .card-front .brand-dot { background: var(--sky-blue); }
  .card-back .brand { left: 110px; top: 90px; font-size: 32px; color: var(--white); }
  .card-back .brand-dot { background: var(--white); }
  .holder-name {
    position: absolute; left: 346px; top: 160px;
    font-size: 18px; font-weight: 700; color: var(--ink-dark);
  }
  .holder-role {
    position: absolute; right: 16px; top: 190px;
    font-size: 11px; color: var(--white);
  }
  .contact-list {
    position: absolute; left: 20px; top: 236px;
    list-style: none; color: var(--white); font-size: 14px;
  }
  .contact-list li { display: flex; align-items: center; gap: 8px; margin-bottom: 5px; }
  .contact-list svg { width: 13px; height: 13px; flex: none; }
  .service-list {
    position: absolute; left: 30px; top: 196px;
    list-style: none; color: var(--ink-dark); font-size: 15px; font-weight: 600;
  }
  .service-list li { display: flex; align-items: center; gap: 10px; margin-bottom: 4px; }
  .service-list li::before {
    content: ""; width: 11px; height: 11px; border-radius: 50%; background: var(--white);
  }
</style>
</head>
<body>

  <section class="card card-front" aria-label="Business card front">
    <svg class="front-bands" viewBox="0 0 520 297" width="520" height="297" aria-hidden="true">
      <path d="M0,200 H322 L332,150 H520 V297 H0 Z" fill="var(--leaf-green)"/>
      <path d="M0,207 H328 L334,186 H520 V297 H0 Z" fill="var(--sky-blue)"/>
    </svg>
    <div class="brand"><span class="brand-dot"></span>Summit BladeAir, Inc.</div>
    <p class="holder-name">Dennis Tollerby</p>
    <p class="holder-role">Owner</p>
    <ul class="contact-list">
      <li>
        <svg viewBox="0 0 24 24" aria-hidden="true"><path fill="#fff" d="M6.6 10.8a15.1 15.1 0 0 0 6.6 6.6l2.2-2.2a1 1 0 0 1 1-.25 11.4 11.4 0 0 0 3.6.57 1 1 0 0 1 1 1V20a1 1 0 0 1-1 1A17 17 0 0 1 3 4a1 1 0 0 1 1-1h3.5a1 1 0 0 1 1 1c0 1.25.2 2.46.57 3.6a1 1 0 0 1-.25 1z"/></svg>
        626-418-7352
      </li>
      <li>
        <svg viewBox="0 0 24 24" aria-hidden="true"><rect x="2" y="5" width="20" height="14" fill="none" stroke="#fff" stroke-width="2"/><path d="M2 5l10 8 10-8" fill="none" stroke="#fff" stroke-width="2"/></svg>
        SummitBladeair@Kestmail.com
      </li>
    </ul>
  </section>

  <section class="card card-back" aria-label="Business card back">
    <div class="brand"><span class="brand-dot"></span>Summit BladeAir, Inc.</div>
    <ul class="service-list">
      <li>Aerial Filming &amp; Photography</li>
      <li>Flight School</li>
      <li>Helicopter Tours (In that order)</li>
    </ul>
  </section>

</body>
</html>
```